Web Site Mock Up's for a Dog Food Business

We are a supplier of bespoke dog food. We tailor our dog food to meet the dogs needs.We are looking for ideas (mock ups) of design ideas for our new web site - Just mock ups - web site will follow if we are happy with the mock ups.I have included our logo (PSD file). I have also included a rough (please don’t copy) home page with the information we would ideally like on the page. Note the page will have sliders at the top, we have done two example sliders, and included a video to be included.I have also enclosed the questions we need to find out in order to develop a dogs food.I would like to see a home page, and a tell us about your dog page.Would like mock ups as PSD files, so we can play around with.I am open to ideas and better designs. DO NOT JUST COPY MY LAYOUTSome of our competitors sites include www.tails.comwww.paws.comwww.parcelpet.comwww.growlingtums.co.ukI want a clean, bright easy to navigate site. Happy to play around with colours - doesn’t have to be the browns I have used. Happy to use both infographics and photo of real dogs, but I do want site to look like the best food available for dogs.Web site will be a database driven site, with around 10 -15 pages plus about 60 dynamic database driven pages of products (all same layout )Look forward to receiving your ideas.

```html
<!DOCTYPE html>
<html lang="en">
<head>
<meta charset="utf-8">
<title>kibblora.co.uk — Home</title>
<link href="https://fonts.googleapis.com/css2?family=Montserrat:wght@300;400;500;600;700&display=swap" rel="stylesheet">
<style>
:root{
  --orange:#f15a22;
  --ink:#222;
  --text:#555;
  --muted:#8a8a8a;
  --light:#f4f4f4;
  --line:#dcdcdc;
  --brown:#8a5a30;
  --brown-dark:#5c3a1e;
  --footer:#1d1d1f;
  --white:#fff;
}
*{box-sizing:border-box;margin:0;padding:0}
html,body{width:1200px;height:5056px;overflow:hidden}
body{font-family:'Montserrat',sans-serif;color:var(--ink);background:var(--white);position:relative}
.abs{position:absolute}
.btn{position:absolute;background:var(--orange);color:var(--white);font-weight:600;font-size:14px;letter-spacing:1.5px;text-transform:uppercase;border-radius:24px;display:flex;align-items:center;justify-content:center;height:40px}
.photo{position:absolute}

/* top bar */
.topbar{top:0;left:0;width:1200px;height:47px;background:#fafafa;border-bottom:1px solid #eee}
.topbar .login{position:absolute;top:8px;left:945px;width:78px;height:28px;border-radius:14px;background:#ddd;font-size:12px;font-weight:600;display:flex;align-items:center;justify-content:center}
.topbar .contact{position:absolute;top:8px;left:1030px;width:100px;height:28px;font-size:12px;font-weight:600;display:flex;align-items:center;justify-content:center}

/* nav */
.nav{top:47px;left:0;width:1200px;height:105px;background:var(--white)}
.nav a{position:absolute;top:50px;font-size:15px;font-weight:500;color:#444;text-decoration:none}
.brand{position:absolute;left:505px;top:20px;width:190px;height:70px;display:flex;align-items:center;justify-content:center;gap:8px;font-size:16px;font-weight:700;color:var(--ink)}
.brand i{width:14px;height:14px;border-radius:50%;background:var(--orange);display:block}

/* hero */
.hero{top:152px;left:0;width:1200px;height:573px;background:linear-gradient(90deg,#6b4324,#a06a3a 45%,#8c5a2e 70%,#6a4222)}
.hero .arrow{position:absolute;top:253px;width:40px;height:40px;border-radius:50%;background:rgba(0,0,0,.55);display:flex;align-items:center;justify-content:center}
.hero .watch{position:absolute;top:288px;left:0;width:1200px;display:flex;justify-content:center;align-items:center;gap:10px;color:var(--white);font-size:13px}
.hero .watch span.play{width:34px;height:34px;border-radius:50%;background:var(--white);display:flex;align-items:center;justify-content:center}
.hero h1{position:absolute;top:330px;left:0;width:1200px;text-align:center;color:var(--white);font-size:36px;font-weight:600;line-height:46px}
.notch{position:absolute;left:560px;top:702px;width:80px;height:24px}

/* how it works */
.how{top:725px;left:0;width:1200px;height:562px;background:var(--light)}
.section-title{position:absolute;left:0;width:1200px;text-align:center;font-size:34px;font-weight:300;color:#333}
.section-title b{font-weight:700}
.step{position:absolute;top:150px;width:230px}
.step svg{display:block;margin-bottom:22px}
.step .num{font-size:12px;color:var(--muted)}
.step h3{font-size:16px;font-weight:700;margin:4px 0 10px}
.step p{font-size:12px;line-height:18px;color:var(--muted)}
.chev{position:absolute;top:168px}

/* our foods */
.foods{top:1287px;left:0;width:1200px;height:499px;background:linear-gradient(180deg,#d6c2a8,#c5a37c 40%,#a87a4c)}
.foods .veil{position:absolute;left:0;top:120px;width:1200px;height:140px;background:rgba(255,255,255,.55)}
.foods h2{position:absolute;top:140px;width:1200px;text-align:center;font-size:34px;font-weight:300}
.foods p{position:absolute;top:194px;width:1200px;text-align:center;font-size:15px;line-height:25px;color:#333}

/* food rows */
.food h2{font-size:30px;font-weight:400;color:#222;margin-bottom:18px}
.food h2 b{font-weight:700}
.food p{font-size:16px;line-height:26px;color:#444}
.food{position:absolute;width:500px}

/* testimonials */
.quote{position:absolute;top:3909px;width:337px;height:270px;background:#f0f0f0;padding:22px 30px}
.quote .mark{font-size:60px;font-weight:700;line-height:40px;color:#333;height:40px}
.quote p{font-size:14px;line-height:21px;color:#444;margin-top:6px}
.quote h4{font-size:13px;font-weight:700;margin-top:16px}

/* faq */
.faq-q{position:absolute;left:67px;width:1058px;height:36px;background:#eee;border:1px solid var(--line);font-size:14px;color:#555;padding-left:24px;display:flex;align-items:center}
.faq-a{position:absolute;left:67px;top:4334px;width:1058px;height:131px;border:1px solid var(--line);padding:14px 24px}
.faq-a h4{font-size:14px;font-weight:600;margin-bottom:8px}
.faq-a p{font-size:12px;line-height:19px;color:var(--muted)}

/* footer */
.footer{top:4617px;left:0;width:1200px;height:439px;background:var(--footer);color:var(--white)}
.footer h3{position:absolute;top:80px;font-size:30px;font-weight:600}
.links{position:absolute;left:67px;top:145px;list-style:none}
.links li{font-size:13px;line-height:33px;display:flex;align-items:center;gap:14px}
.links li::before{content:"";width:0;height:0;border-left:5px solid #fff;border-top:4px solid transparent;border-bottom:4px solid transparent}
.email{position:absolute;left:431px;top:138px;width:330px;height:42px;background:var(--white);color:#333;font-size:13px;font-weight:600;padding-left:16px;display:flex;align-items:center}
.social{position:absolute;top:258px;width:16px;height:16px;background:#cfcfcf;border-radius:2px}
.contact-row{position:absolute;left:870px;display:flex;gap:20px;font-size:13px;line-height:21px}
.copy{position:absolute;top:400px;width:1200px;text-align:center;font-size:12px}
</style>
</head>
<body>

<div class="abs topbar">
  <div class="login">LOG IN</div>
  <div class="contact">CONTACT US</div>
</div>

<nav class="abs nav">
  <a style="left:158px">Home</a>
  <a style="left:243px">Our Food</a>
  <a style="left:356px">How it Works</a>
  <div class="brand"><i></i>kibblora.co.uk</div>
  <a style="left:728px">Pricing</a>
  <a style="left:822px">Customer Reviews</a>
  <a style="left:1007px">FAQ</a>
</nav>

<section class="abs hero" role="img" aria-label="Warm brown hero photograph of a basset hound sitting in a large dog bowl with a golden dog in the background">
  <div class="arrow" style="left:115px"><svg width="12" height="14" viewBox="0 0 12 14"><path d="M9 1 3 7l6 6" fill="none" stroke="#fff" stroke-width="2.5"/></svg></div>
  <div class="arrow" style="left:1038px"><svg width="12" height="14" viewBox="0 0 12 14"><path d="M3 1l6 6-6 6" fill="none" stroke="#fff" stroke-width="2.5"/></svg></div>
  <div class="watch"><span class="play"><svg width="12" height="14" viewBox="0 0 12 14"><path d="M2 1l9 6-9 6z" fill="#222"/></svg></span>Watch the Video</div>
  <h1>Food unique as your dog blended<br>using the finest ingredients</h1>
  <div class="btn" style="left:435px;top:434px;width:330px">Tell us about your dog</div>
</section>
<svg class="notch" viewBox="0 0 80 24"><path d="M0 24 C20 24 28 0 40 0 C52 0 60 24 80 24Z" fill="#f4f4f4"/></svg>

<section class="abs how">
  <h2 class="section-title" style="top:48px">How it <b>works</b></h2>

  <div class="step" style="left:67px">
    <svg width="100" height="80" viewBox="0 0 100 80" fill="none" stroke="#888" stroke-width="2"><path d="M20 70 Q18 40 40 38 L52 22 Q58 16 62 24 L70 20 Q76 30 66 36 Q60 46 62 70 M30 70 L30 56 M48 70 L50 56 M40 38 Q30 20 18 30"/><circle cx="61" cy="27" r="1.5" fill="#888"/></svg>
    <div class="num">Step 01</div>
    <h3>Tell Us about your Dog</h3>
    <p>Tell about your dogs age, sex, breed, weight and body condition, how active they are, any health conditions, or special dietary requirements they need.</p>
  </div>
  <svg class="chev" style="left:320px" width="30" height="50" viewBox="0 0 30 50"><path d="M5 3l20 22L5 47" fill="none" stroke="#bbb" stroke-width="2"/></svg>

  <div class="step" style="left:492px">
    <svg width="100" height="80" viewBox="0 0 100 80" fill="none" stroke="#888" stroke-width="2"><path d="M32 8h36v8l4 8v48H28V24l4-8z M32 16h36"/><circle cx="50" cy="46" r="10"/><path d="M46 44h8M50 40v12"/></svg>
    <div class="num">Step 02</div>
    <h3>We create your Food</h3>
    <p>You have full control on your subscription, pause, take holidays or end when you want.</p>
  </div>
  <svg class="chev" style="left:745px" width="30" height="50" viewBox="0 0 30 50"><path d="M5 3l20 22L5 47" fill="none" stroke="#bbb" stroke-width="2"/></svg>

  <div class="step" style="left:910px">
    <svg width="100" height="80" viewBox="0 0 100 80" fill="none" stroke="#888" stroke-width="2"><path d="M22 58h48V26H22z M70 36h14l8 12v10H70 M36 26V12h20v14"/><circle cx="34" cy="62" r="6"/><circle cx="80" cy="62" r="6"/><path d="M4 34h12M8 44h10"/></svg>
    <div class="num">Step 03</div>
    <h3>We Delivery</h3>
    <p>We deliver your food FREE as and when you need it, so you never run out.</p>
  </div>

  <div class="btn" style="left:383px;top:468px;width:434px">You pay one simple monthly amount</div>
</section>

<section class="abs foods" role="img" aria-label="Photograph of a dog eating from a full bowl of dry dog food on a light background">
  <div class="veil"></div>
  <h2>Our <b>Foods</b></h2>
  <p>We develop and create your dogs best food using the finest ingredients, based on your dogs requirements.<br>Our foods are developed by pet nutritionalists, approved by vets and enjoyed by all dogs.</p>
  <div class="btn" style="left:520px;top:288px;width:160px">Start Now</div>
</section>

<!-- Senior -->
<div class="food" style="left:72px;top:1880px"><h2>Senior <b>Food</b></h2><p>The right balance of protein and energy to help reduce joint pain, while maintaining Weight to keep your dog active</p></div>
<div class="btn" style="left:67px;top:2040px;width:188px">Tell me more</div>
<div class="photo" style="left:613px;top:1823px;width:512px;height:285px;background:linear-gradient(135deg,#e8dccb,#c9a77c 55%,#8e6a44)" role="img" aria-label="Senior dog lying beside a bowl of food on a wooden floor"></div>

<!-- Adult -->
<div class="photo" style="left:74px;top:2138px;width:512px;height:288px;background:linear-gradient(135deg,#7a5a40,#c59a62 50%,#e4cfa6)" role="img" aria-label="Woman offering a bowl of food to a golden retriever"></div>
<div class="food" style="left:615px;top:2180px"><h2>Adult <b>Food</b></h2><p>Careful balance of proteins, fats and oils, minerals, vitamins and carbohydrates are needed as an adult and differ between breeds</p></div>
<div class="btn" style="left:609px;top:2340px;width:188px">Tell me more</div>

<!-- Puppy -->
<div class="food" style="left:72px;top:2500px"><h2>Puppy <b>Food</b></h2><p>A well balanced and nutritious range of foods to meet the needs of growing puppies of all breeds.</p></div>
<div class="btn" style="left:67px;top:2640px;width:188px">Tell me more</div>
<div class="photo" style="left:613px;top:2458px;width:512px;height:288px;background:linear-gradient(180deg,#f7f7f7,#e9e2da 60%,#b88a5c)" role="img" aria-label="Puppy sitting among scattered kibble next to a dog bowl"></div>

<!-- Health -->
<div class="photo" style="left:74px;top:2775px;width:512px;height:288px;background:linear-gradient(135deg,#dfe6ef,#9fb6d4 45%,#d8c29a)" role="img" aria-label="Vet in blue scrubs examining a golden retriever"></div>
<div class="food" style="left:613px;top:2815px"><h2>Foods for <b>Health Problems</b></h2><p>Itchy Skin ?<br>Joint Problems ? Sensitive tummy?<br>We will create a food to suit your dogs needs</p></div>
<div class="btn" style="left:609px;top:2968px;width:188px">Tell me more</div>

<!-- Weight -->
<div class="food" style="left:72px;top:3130px"><h2>Weight <b>Control Food</b></h2><p>Weight control is about still giving your dog a filling and tasty food that will satisfy your dogs appetite whilst keeping off extra weight.</p></div>
<div class="btn" style="left:67px;top:3290px;width:188px">Tell me more</div>
<div class="photo" style="left:613px;top:3088px;width:512px;height:292px;background:linear-gradient(180deg,#fafafa,#e6d6c2 55%,#7a5a3c)" role="img" aria-label="Small terrier puppy sitting in a metal food bowl"></div>

<!-- Specialist -->
<div class="photo" style="left:74px;top:3432px;width:512px;height:288px;background:linear-gradient(135deg,#e4d3b0,#c6a46e 50%,#8e6a42)" role="img" aria-label="Labrador looking up at a hand holding a bowl of food"></div>
<div class="food" style="left:613px;top:3470px"><h2>Specialist <b>Foods</b></h2><p>We provide grain free and hypoallergenic foods for fussy eaters, dogs with allergies and food intolerances.</p></div>
<div class="btn" style="left:609px;top:3625px;width:188px">Tell me more</div>

<!-- Testimonials -->
<h2 class="section-title" style="top:3822px;font-size:30px">What our <b>Customers Say</b></h2>
<div class="quote" style="left:67px"><div class="mark">“</div><p>"I have 3 dogs all on different foods. No more trips to the shops fetching massive bags of food. This works for me and my dogs love it."</p><h4>Tamsin with Rufus - Ashby</h4></div>
<div class="quote" style="left:431px"><div class="mark">“</div><p>"My dog is a really fussy eater and has a very sensitive stomach. I found my ideal food here, which suits him. GREAT !"</p><h4>Ned, Pip and Bramble - Holmfirth</h4></div>
<div class="quote" style="left:795px"><div class="mark">“</div><p>"My dog is on the itchy skin formula, and although she still itches sometimes its much better. Its cheaper than the vets options, and a great service."</p><h4>Mrs Carrow with Bess - Dorset</h4></div>

<!-- FAQ -->
<h2 class="section-title" style="top:4220px;font-size:30px">Faqs</h2>
<div class="faq-q" style="top:4290px">Q : Lorem ipsum dolor sit amet, consectetur adipiscing elit, sed do eiusmod tempor incididunt ?</div>
<div class="faq-a"><h4>Answer :</h4><p>Each recipe is mixed to order from the details you share about your dog, checked by our nutrition team and packed fresh. You can change portions, pause deliveries or switch recipes at any time from your account page, and our team is always happy to help.</p></div>
<div class="faq-q" style="top:4482px">Q : Lorem ipsum dolor sit amet, consectetur adipiscing elit, sed do eiusmod tempor incididunt ?</div>
<div class="faq-q" style="top:4533px">Q : Lorem ipsum dolor sit amet, consectetur adipiscing elit, sed do eiusmod tempor incididunt ?</div>

<!-- Footer -->
<footer class="abs footer">
  <h3 style="left:67px">Quick Links</h3>
  <ul class="links"><li>Home</li><li>Our Food</li><li>How it Works</li><li>Pricing</li><li>Customer Reviews</li><li>FAQ</li></ul>

  <h3 style="left:431px">Newsletter Subscribe</h3>
  <div class="email">Enter Email id
    <svg style="position:absolute;right:16px" width="16" height="12" viewBox="0 0 16 12"><rect x="1" y="1" width="14" height="10" fill="none" stroke="#333" stroke-width="1.5"/><path d="M1 1l7 6 7-6" fill="none" stroke="#333" stroke-width="1.5"/></svg>
  </div>
  <div class="btn" style="left:431px;top:198px;width:134px;height:36px">Subscribe</div>
  <div class="social" style="left:441px"></div>
  <div class="social" style="left:475px"></div>

  <h3 style="left:870px">Contact us</h3>
  <div class="contact-row" style="top:150px"><svg width="14" height="18" viewBox="0 0 14 18"><path d="M7 1a6 6 0 0 0-6 6c0 4.5 6 10 6 10s6-5.5 6-10a6 6 0 0 0-6-6z" fill="#fff"/><circle cx="7" cy="7" r="2.2" fill="#1d1d1f"/></svg><span>2417 Larkfield Rd,<br>Ellersby, OH 44902</span></div>
  <div class="contact-row" style="top:222px"><svg width="16" height="16" viewBox="0 0 16 16"><path d="M3 1l3 3-2 2c1 2 3 4 5 5l2-2 3 3-2 3C6 15 1 10 1 3z" fill="#fff"/></svg><span>1-800-555-0142</span></div>
  <div class="contact-row" style="top:268px"><svg width="16" height="12" viewBox="0 0 16 12"><rect width="16" height="12" fill="#fff"/><path d="M0 0l8 7 8-7" fill="none" stroke="#1d1d1f" stroke-width="1.5"/></svg><span>hello@kibblora.co.uk</span></div>

  <div class="copy">© 2018 | www.kibblora.co.uk</div>
</footer>

</body>
</html>
```